I need a business card design for a real estate finance, development and management business. We deal with high net worth clients and ask that the business card be neat, clean and sophisticated. We like the attached logo design, font and color and want to incorporate all this into the business card.

Industry/Entity Type

Real Estate

```html
<!DOCTYPE html>
<html lang="en">
<head>
<meta charset="utf-8">
<title>Silver Pond – Business Card</title>
<link href="https://fonts.googleapis.com/css2?family=Open+Sans:wght@400;600;700&display=swap" rel="stylesheet">
<style>
  :root {
    --brand-blue: #235e9c;
    --card-white: #ffffff;
    --backdrop: #ebebeb;
    --card-shadow: rgba(0, 0, 0, 0.12);
  }
  * { box-sizing: border-box; margin: 0; padding: 0; }
  html, body {
    width: 1200px; height: 947px; overflow: hidden;
    background: var(--backdrop);
    font-family: "Open Sans", Arial, sans-serif;
    color: var(--brand-blue);
  }
  .sheet {
    width: 1200px; height: 947px;
    display: flex; align-items: center; justify-content: center; gap: 60px;
  }
  .card {
    position: relative;
    width: 520px; height: 297px;
    background: var(--card-white);
    box-shadow: 0 6px 20px var(--card-shadow);
    overflow: hidden;
  }
  .card::before, .card::after {
    content: ""; position: absolute; left: 0; right: 0; height: 18px;
    background: var(--brand-blue);
  }
  .card::before { top: 0; }
  .card::after { bottom: 0; }

  /* contact side */
  .contact-side .person { position: absolute; left: 30px; top: 42px; }
  .person-name { font-size: 22px; font-weight: 400; line-height: 1.15; }
  .person-name strong { font-weight: 700; }
  .person-title { font-size: 15px; margin-top: 2px; }
  .contact-list {
    position: absolute; left: 30px; top: 132px;
    list-style: none; font-size: 15.5px; line-height: 26px;
  }
  .contact-list li { display: flex; align-items: center; gap: 12px; }
  .contact-icon { width: 18px; height: 18px; flex: none; fill: var(--brand-blue); }
  .contact-icon.blank { fill: none; }
  .contact-side .brand-name {
    position: absolute; right: 30px; top: 50%;
    transform: translateY(-50%) rotate(180deg);
    writing-mode: vertical-rl;
    font-size: 26px; font-weight: 600; letter-spacing: 2px; text-transform: uppercase;
  }

  /* logo side */
  .logo-side { display: flex; align-items: center; justify-content: center; }
  .logo-side .brand-name {
    font-size: 42px; font-weight: 600; letter-spacing: 3px; text-transform: uppercase;
  }
</style>
</head>
<body>
<main class="sheet">
  <section class="card contact-side">
    <div class="person">
      <h1 class="person-name"><strong>Daniel</strong> R. Whitford</h1>
      <p class="person-title">Managing Partner</p>
    </div>
    <ul class="contact-list">
      <li>
        <svg class="contact-icon" viewBox="0 0 20 20" aria-hidden="true"><path d="M10 2 1 10h3v8h5v-5h2v5h5v-8h3z"/></svg>
        18 Harbor View Rd. Westport, CT 06880
      </li>
      <li>
        <svg class="contact-icon" viewBox="0 0 20 20" aria-hidden="true"><path d="M4 2h4l2 5-2.5 1.5a11 11 0 0 0 4 4L13 10l5 2v4a2 2 0 0 1-2 2A14 14 0 0 1 2 4a2 2 0 0 1 2-2z"/></svg>
        203 555 0147
      </li>
      <li>
        <svg class="contact-icon" viewBox="0 0 20 20" aria-hidden="true"><rect x="2" y="3" width="16" height="11" rx="1"/><rect x="7" y="15" width="6" height="2"/></svg>
        drwhitford@silverpondcapital.net
      </li>
      <li>
        <svg class="contact-icon blank" viewBox="0 0 20 20" aria-hidden="true"></svg>
        www.silverpondcapital.net
      </li>
    </ul>
    <p class="brand-name">Silver Pond</p>
  </section>

  <section class="card logo-side">
    <p class="brand-name">Silver Pond</p>
  </section>
</main>
</body>
</html>
```